Business Card Update, need to bring life to the card, two sided color

We need a new business card design, are moving and changing addresses and need a new look, we have the logos already attached but need a new style moving forward. Can incorporate the color of the logo (The Green) as well, maybe a solid back? We deal with safety products revolving around static electricity and safety lighting. Would like to keep same font in second logo as well.

Target Market(s)

Electrical Safety, Lighting

Contact Information for Business Card

Dale Fenwick
Vice President
Office: 770-555-4821
Cell: 770-555-3067
dale@tkfenwick.example
www.tkfenwick.example
4700 West Harbor Boulevard
Suite #150
Roswell, GA 30076

Font styles to use
Serif
Sans Serif

Requirements
Must have
• Since 1918
Nice to have
• Could use the 100 Year Logo for back of card, would like the back of card to be the same green as logo.
Should not have
• No black cards please.

```html
<!DOCTYPE html>
<html lang="en">
<head>
<meta charset="utf-8">
<title>T.K. Fenwick Business Card</title>
<link rel="stylesheet" href="https://fonts.googleapis.com/css2?family=Archivo+Black&family=Roboto:ital,wght@0,400;0,500;1,400&display=swap">
<style>
  :root {
    --brand-green: #05995a;
    --card-white: #ffffff;
    --ink-grey: #3a3a3a;
    --page-bg: #e6e8e7;
  }
  * { box-sizing: border-box; margin: 0; padding: 0; }
  html, body { width: 1200px; height: 768px; overflow: hidden; }
  body {
    background: var(--page-bg);
    font-family: "Roboto", sans-serif;
    position: relative;
  }
  .card {
    position: absolute;
    top: 230px;
    width: 540px;
    height: 309px;
    border-radius: 18px;
    overflow: hidden;
    box-shadow: 0 6px 18px rgba(0,0,0,0.18);
  }
  .card-front { left: 40px; background: var(--card-white); }
  .card-back { left: 620px; background: var(--brand-green); color: var(--card-white); }

  /* front */
  .brand-lockup {
    position: absolute;
    left: 88px;
    top: 100px;
    display: flex;
    align-items: center;
    gap: 14px;
    color: var(--brand-green);
  }
  .brand-dot {
    width: 64px; height: 64px;
    border-radius: 50%;
    background: var(--brand-green);
    flex: none;
  }
  .brand-name {
    font-family: "Archivo Black", sans-serif;
    font-size: 27px;
    line-height: 1;
  }
  .brand-sub {
    font-family: "Archivo Black", sans-serif;
    font-size: 12.5px;
    margin-top: 3px;
    margin-left: 20px;
  }
  .since-line {
    position: absolute;
    left: 0; right: 0;
    bottom: 92px;
    text-align: center;
    font-size: 12px;
    font-weight: 500;
    letter-spacing: 3px;
    text-transform: uppercase;
    color: var(--brand-green);
  }
  .front-web {
    position: absolute;
    left: 0; right: 0;
    bottom: 56px;
    text-align: center;
    font-size: 13px;
    letter-spacing: 5px;
    color: var(--ink-grey);
  }

  /* back */
  .contact-block {
    position: absolute;
    left: 34px;
    top: 26px;
  }
  .person-name {
    font-family: "Archivo Black", sans-serif;
    font-size: 22px;
    line-height: 1;
  }
  .person-title {
    font-style: italic;
    font-size: 14px;
    margin-top: 2px;
  }
  .address {
    font-size: 13.5px;
    line-height: 1.2;
    margin-top: 14px;
  }
  .contact-list { list-style: none; margin-top: 8px; font-size: 13.5px; }
  .contact-list li {
    display: flex;
    align-items: center;
    gap: 9px;
    line-height: 1.25;
  }
  .contact-icon { width: 12px; height: 12px; flex: none; }
  .back-brand {
    position: absolute;
    left: 34px;
    bottom: 28px;
    font-family: "Archivo Black", sans-serif;
  }
  .back-brand .brand-name { font-size: 25px; }
  .back-brand .brand-sub { font-size: 11.5px; margin-left: 4px; }
  .product-art {
    position: absolute;
    right: 0;
    top: 0;
    width: 150px;
    height: 100%;
    background: var(--card-white);
  }
</style>
</head>
<body>

<section class="card card-front" aria-label="Card front">
  <div class="brand-lockup">
    <span class="brand-dot"></span>
    <div>
      <div class="brand-name">T.K. Fenwick</div>
      <div class="brand-sub">Manufacturing Company, Inc.</div>
    </div>
  </div>
  <p class="since-line">Since 1918</p>
  <p class="front-web">www.tkfenwick.example</p>
</section>

<section class="card card-back" aria-label="Card back">
  <div class="contact-block">
    <h1 class="person-name">Dale Fenwick</h1>
    <p class="person-title">Vice President</p>
    <p class="address">4700 West Harbor Boulevard, Suite #150<br>Roswell, GA 30076</p>
    <ul class="contact-list">
      <li>
        <svg class="contact-icon" viewBox="0 0 12 12"><path fill="#fff" d="M2.5 0.8 4.3 2.6 3.2 4.2c.8 1.7 2 2.9 3.6 3.6l1.6-1.1 1.8 1.8-1.3 2C5 10.1 1.8 6.9 0.5 2.1z"/></svg>
        770 555 4821
      </li>
      <li>
        <svg class="contact-icon" viewBox="0 0 12 12"><rect x="2.5" y="0.5" width="7" height="11" rx="1.2" fill="none" stroke="#fff"/><circle cx="6" cy="9.6" r=".7" fill="#fff"/></svg>
        770 555 3067
      </li>
      <li>
        <svg class="contact-icon" viewBox="0 0 12 12"><rect x="3" y="1" width="6" height="3.5" fill="#fff"/><rect x="0.5" y="5" width="11" height="5" rx="1" fill="#fff"/></svg>
        770 555 7302
      </li>
      <li>
        <svg class="contact-icon" viewBox="0 0 12 12"><rect x="0.5" y="2" width="11" height="8" fill="#fff"/><path d="M0.5 2 6 6.5 11.5 2" fill="none" stroke="#05995a"/></svg>
        dale@tkfenwick.example
      </li>
      <li>
        <svg class="contact-icon" viewBox="0 0 12 12"><circle cx="6" cy="6" r="5.5" fill="#fff"/><path d="M1 6h10M6 .5c-2.5 3-2.5 8 0 11M6 .5c2.5 3 2.5 8 0 11" fill="none" stroke="#05995a" stroke-width=".8"/></svg>
        www.tkfenwick.example
      </li>
    </ul>
  </div>
  <div class="back-brand">
    <div class="brand-name">T.K. Fenwick</div>
    <div class="brand-sub">Manufacturing Company, Inc.</div>
  </div>
  <div class="product-art" role="img" aria-label="Line illustration of a grounding safety device in green outline on white"></div>
</section>

</body>
</html>
```